Harbor Crestline (Business Card Design)

Need business cards designed. Something modern, chic, and sleek. Mabye the back of the card should be the navy blue that is in the logo and then just the logo on the back.

Target Market(s)

Those in the hotel, office, and renovation industry

Contact Information for Business Card

1. Logo 2. Dorian Fenwick 3. CEO/Founder 4. Phone: (833) HarbCre / (833) 427-2731 5. Email: dorian@theharborcrestline.com 6. Website: www.theharborcrestline.com

Font styles to use
Other font styles liked:
• Look at the logo font and base the font for everything else off of that.

Colors
0054AA
0677BA
7BADD7
CADEEF
E8F1F8

Requirements
Must have
• Colors that are associated in the logo
Nice to have
• Sleek modern clean and chic design.

```html
<!DOCTYPE html>
<html lang="en">
<head>
<meta charset="utf-8">
<title>Harbor Crestline – Business Card</title>
<link href="https://fonts.googleapis.com/css2?family=Montserrat:wght@600;700&family=Open+Sans:wght@400;600&display=swap" rel="stylesheet">
<style>
  :root {
    --navy: #0e1a4a;
    --navy-light: #1c2a66;
    --navy-deep: #0a1238;
    --gold: #d4a94a;
    --white: #ffffff;
    --stage: #e6e8ee;
  }
  * { box-sizing: border-box; margin: 0; padding: 0; }
  html, body { width: 1200px; height: 780px; overflow: hidden; }
  body {
    background: var(--stage);
    position: relative;
    font-family: "Open Sans", Arial, sans-serif;
  }
  .card {
    position: absolute;
    width: 540px;
    height: 309px;
    border-radius: 22px;
    background: var(--navy);
    border: 3px solid var(--gold);
    overflow: hidden;
    box-shadow: 0 14px 30px rgba(10, 18, 56, 0.25);
  }
  .card--front { left: 40px; top: 236px; }
  .card--back { left: 620px; top: 236px; }

  .monogram-pattern {
    position: absolute;
    inset: 0;
    background: linear-gradient(160deg, var(--navy-light) 0%, var(--navy) 55%, var(--navy-deep) 100%);
  }
  .front-wordmark {
    position: absolute;
    left: 0; right: 0; top: 50%;
    transform: translateY(-50%);
    display: flex;
    align-items: center;
    justify-content: center;
    gap: 14px;
  }
  .wordmark-text {
    font-family: "Montserrat", Arial, sans-serif;
    font-weight: 700;
    color: var(--white);
    text-transform: uppercase;
    letter-spacing: 2px;
  }
  .front-wordmark .wordmark-text { font-size: 36px; }
  .wordmark-square { background: var(--gold); flex: none; }
  .front-wordmark .wordmark-square { width: 16px; height: 16px; }

  .name-block {
    position: absolute;
    right: 0;
    top: 38px;
    display: flex;
    align-items: flex-start;
  }
  .name-text { text-align: right; padding-right: 14px; }
  .person-name {
    font-family: "Montserrat", Arial, sans-serif;
    font-weight: 700;
    font-size: 30px;
    line-height: 1.05;
    color: var(--gold);
  }
  .person-title {
    font-size: 14px;
    font-weight: 600;
    color: var(--white);
    margin-top: 4px;
  }
  .gold-bar { width: 22px; height: 58px; background: var(--gold); }

  .back-details {
    position: absolute;
    left: 34px;
    bottom: 30px;
    color: var(--white);
  }
  .back-wordmark { display: flex; align-items: center; gap: 8px; margin-bottom: 14px; }
  .back-wordmark .wordmark-text { font-size: 18px; }
  .back-wordmark .wordmark-square { width: 10px; height: 10px; }
  .address { font-size: 13px; line-height: 1.45; margin-bottom: 16px; }
  .contact-list { list-style: none; font-size: 13px; line-height: 1.6; }
  .contact-list li { display: flex; align-items: center; gap: 9px; }
  .contact-list svg { width: 13px; height: 13px; flex: none; }
</style>
</head>
<body>

<section class="card card--front" aria-label="Card front">
  <div class="monogram-pattern" role="img" aria-label="Repeating tone-on-tone monogram pattern across the card"></div>
  <div class="front-wordmark">
    <span class="wordmark-square"></span>
    <span class="wordmark-text">Harbor Crestline</span>
  </div>
</section>

<section class="card card--back" aria-label="Card back">
  <div class="name-block">
    <div class="name-text">
      <div class="person-name">Dorian Fenwick</div>
      <div class="person-title">CEO/Founder</div>
    </div>
    <div class="gold-bar"></div>
  </div>

  <div class="back-details">
    <div class="back-wordmark">
      <span class="wordmark-square"></span>
      <span class="wordmark-text">Harbor Crestline</span>
    </div>
    <p class="address">4120 Larkmoor Ave<br>Suite 210, Ellisford, MD 21987</p>
    <ul class="contact-list">
      <li>
        <svg viewBox="0 0 24 24" fill="#d4a94a" aria-hidden="true"><path d="M6.6 10.8a15.1 15.1 0 0 0 6.6 6.6l2.2-2.2a1 1 0 0 1 1-.25 11.4 11.4 0 0 0 3.6.57 1 1 0 0 1 1 1V20a1 1 0 0 1-1 1A17 17 0 0 1 3 4a1 1 0 0 1 1-1h3.5a1 1 0 0 1 1 1c0 1.25.2 2.45.57 3.57a1 1 0 0 1-.25 1z"/></svg>
        (833) HarbCre / (833) 427-2731
      </li>
      <li>
        <svg viewBox="0 0 24 24" fill="none" stroke="#d4a94a" stroke-width="2" aria-hidden="true"><circle cx="12" cy="12" r="9"/><path d="M3 12h18M12 3c3 3 3 15 0 18M12 3c-3 3-3 15 0 18"/></svg>
        www.theharborcrestline.com
      </li>
      <li>
        <svg viewBox="0 0 24 24" fill="none" stroke="#d4a94a" stroke-width="2" aria-hidden="true"><rect x="3" y="5" width="18" height="14" rx="1"/><path d="M3 6l9 7 9-7"/></svg>
        dorian@theharborcrestline.com
      </li>
    </ul>
  </div>
</section>

</body>
</html>
```